Bespoke Builders Business Card Design

We need a business card for an established builder of high quality bespoke homes in Auckland and Northland. We build and renovate homes collaboratively facilitating effective communication between owners, builders, architects, suppliers and tradespeople. We have never built or renovated a home that leaks or has faults. We only use reliable materials. We have never been sued or had legal action taken against us. We are honest builders of bespoke homes not group mass produced homes. Our niche market is in character homes. We practice sustainability and have built a lot of coastal property. We have been in business for over thirty years . We would like to see natural colors of the environment sand,sea and maybe vegetation . The design should communicate quality, sustainability,fair pricing, open communication and the originality of bespoke building. And the fact that the builder is registered.

Industry/Entity Type

Business

Contact Information for Business Card

Rowan Tellick Builders
Ph. 021583917
18 Kestrel Rd Harwood Bay Auckland 0814
PO Box 927 Mangawhai 0583

```html
<!DOCTYPE html>
<html lang="en">
<head>
<meta charset="utf-8">
<title>Rowan Tellick Builders – Business Card</title>
<link rel="stylesheet" href="https://fonts.googleapis.com/css2?family=Tinos:wght@400;700&display=swap">
<style>
  :root {
    --page-bg: #e9e7e3;
    --silver-light: #f4f4f4;
    --silver-mid: #cfcfcf;
    --silver-dark: #9c9c9c;
    --ink: #1c1c1c;
    --ink-soft: #333333;
    --band-dark: #141414;
    --band-mid: #4a4a4a;
    --band-edge: #bdbdbd;
    --card-black: #0c0c0c;
    --card-black-sheen: #2a2a2a;
    --paper-white: #f2f2f2;
  }
  * { box-sizing: border-box; margin: 0; padding: 0; }
  html, body {
    width: 1200px;
    height: 892px;
    overflow: hidden;
    background: var(--page-bg);
  }
  .canvas {
    width: 1200px;
    height: 892px;
    display: flex;
    flex-direction: column;
    align-items: center;
    justify-content: center;
    gap: 56px;
  }
  .card {
    width: 640px;
    height: 366px;
    position: relative;
    overflow: hidden;
    box-shadow: 0 10px 28px rgba(0,0,0,0.28);
  }

  /* Front side */
  .card--front {
    background: radial-gradient(ellipse at 50% 50%, var(--silver-light) 0%, var(--silver-mid) 60%, var(--silver-dark) 100%);
  }
  .ornament-band {
    position: absolute;
    left: 0;
    width: 100%;
    height: 72px;
    background: linear-gradient(90deg, var(--band-dark) 0%, var(--band-mid) 50%, var(--band-dark) 100%);
    border-top: 2px solid var(--band-edge);
    border-bottom: 2px solid var(--band-edge);
  }
  .ornament-band--top { top: 18px; }
  .ornament-band--bottom { bottom: 30px; }
  .front-content {
    position: absolute;
    top: 92px;
    bottom: 104px;
    left: 0;
    right: 0;
    display: flex;
    flex-direction: column;
    align-items: center;
    justify-content: center;
    font-family: "Tinos", "Times New Roman", serif;
    color: var(--ink);
    text-align: center;
  }
  .company-name {
    font-weight: 700;
    font-size: 34px;
    letter-spacing: 0.5px;
    line-height: 1.1;
  }
  .name-rule {
    width: 380px;
    height: 1px;
    background: var(--ink-soft);
    margin: 10px 0 12px;
  }
  .contact-line {
    font-size: 18px;
    line-height: 1.3;
    color: var(--ink-soft);
  }

  /* Back side */
  .card--back {
    background: linear-gradient(160deg, var(--card-black) 0%, var(--card-black-sheen) 45%, var(--card-black) 70%, var(--card-black-sheen) 100%);
    display: flex;
    align-items: center;
    justify-content: center;
  }
  .back-name {
    font-family: "Tinos", "Times New Roman", serif;
    font-weight: 700;
    font-size: 46px;
    color: var(--paper-white);
    letter-spacing: 1px;
  }
</style>
</head>
<body>
  <main class="canvas">
    <section class="card card--front" aria-label="Business card front">
      <div class="ornament-band ornament-band--top" role="img" aria-label="Ornamental silver scrollwork band"></div>
      <div class="front-content">
        <h1 class="company-name">Rowan Tellick Builders</h1>
        <div class="name-rule"></div>
        <p class="contact-line">021583917</p>
        <p class="contact-line">18 Kestrel Rd Harwood Bay</p>
        <p class="contact-line">Auckland 0814 PO Box 927 Mangawhai 0583</p>
      </div>
      <div class="ornament-band ornament-band--bottom" role="img" aria-label="Ornamental silver scrollwork band"></div>
    </section>

    <section class="card card--back" aria-label="Business card back">
      <h2 class="back-name">Rowan Tellick Builders</h2>
    </section>
  </main>
</body>
</html>
```